TLK Electricial Contracting Services

Hi guys, after a design for my small electrical company, have logo design files to be incorporated into the layout, the basic concept is electrical contracting services for residential, commercial, industrial & data services, image is clean clear and strong,

Card format is to have a nice clean logo on front,with maybe the Residential – commercial – industrial - data, followed with licensed & insured, followed by contact details on backside of the card.

Target Market(s)

Residential, commercial, industrial sectors.

Industry/Entity Type

Electrical

Contact Information for Business Card

TLK logo,
Residential – commercial – industrial - data
REC: 61307
Email: tlk@vornamail.net.au
Phone: 0487 352 019

Requirements
Must have
• Clean & strong design.
Nice to have
• If possible, I would like the logo colours inverted so the text is orange and the background is black on the front of the card, then the backside of the card be the reverse colour
Should not have
• No Sparks, lightning bolts,

```html
<!DOCTYPE html>
<html lang="en">
<head>
<meta charset="utf-8">
<title>TLK Electricial Contracting Services – Business Card</title>
<link href="https://fonts.googleapis.com/css2?family=Aldrich&display=swap" rel="stylesheet">
<style>
  :root {
    --bg: #33414a;
    --card-black: #0b0b0b;
    --brand-orange: #f5832a;
    --white: #ffffff;
    --ink: #111111;
  }
  * { box-sizing: border-box; margin: 0; padding: 0; }
  html, body {
    width: 1200px; height: 900px; overflow: hidden;
    background: var(--bg);
    font-family: "Aldrich", sans-serif;
  }
  .stage { position: relative; width: 1200px; height: 900px; }
  .card {
    position: absolute; left: 300px; width: 600px; height: 345px;
    border-radius: 18px; overflow: hidden;
  }
  .card-front { top: 55px; background: var(--card-black); }
  .card-back  { top: 480px; background: var(--brand-orange); }
  .card-shape { position: absolute; inset: 0; }

  .brand-name { font-size: 84px; line-height: 1; letter-spacing: 1px; }

  /* front */
  .front-brand {
    position: absolute; left: 60px; top: 112px; width: 280px; text-align: center;
  }
  .front-brand .brand-name { color: var(--white); }
  .front-brand .brand-tagline {
    color: var(--brand-orange); font-size: 16px; margin-top: 8px; letter-spacing: .3px;
  }
  .divider {
    position: absolute; left: 352px; top: 70px; width: 3px; height: 200px;
    background: var(--brand-orange);
  }
  .contact { position: absolute; left: 380px; top: 92px; width: 190px; }
  .contact-name { color: var(--brand-orange); font-size: 20px; }
  .contact-role {
    color: var(--white); font-size: 12px; margin-top: 4px;
    border-bottom: 1px solid var(--white); padding-bottom: 1px; width: 180px;
  }
  .contact-list { list-style: none; margin-top: 52px; }
  .contact-list li {
    display: flex; align-items: center; gap: 9px;
    color: var(--brand-orange); font-size: 14px; margin-bottom: 6px;
  }
  .contact-list svg { width: 13px; height: 13px; flex: none; }

  /* back */
  .back-brand { position: absolute; left: 0; right: 0; top: 72px; text-align: center; }
  .back-brand .brand-name { color: var(--ink); }
  .back-brand .brand-tagline { color: var(--ink); font-size: 19px; margin-top: 8px; }
  .services {
    position: absolute; left: 0; right: 0; top: 192px; text-align: center;
    font-size: 18px; line-height: 1.35;
  }
  .services-licence { color: var(--white); }
  .services-sectors { color: var(--ink); }
</style>
</head>
<body>
<main class="stage">

  <section class="card card-front" aria-label="Card front">
    <svg class="card-shape" viewBox="0 0 600 345" aria-hidden="true">
      <path d="M70 0 H530 Q520 14 500 14 H100 Q80 14 70 0 Z" fill="var(--brand-orange)"/>
    </svg>
    <div class="front-brand">
      <div class="brand-name">TLK</div>
      <div class="brand-tagline">Tyler Lane Kirk Electrical</div>
    </div>
    <div class="divider"></div>
    <div class="contact">
      <div class="contact-name">Dale Horner</div>
      <div class="contact-role">Owner</div>
      <ul class="contact-list">
        <li>
          <svg viewBox="0 0 16 16" aria-hidden="true"><path d="M3 1.5l3 .5 1 3.5-2 1.2a8 8 0 0 0 4.3 4.3l1.2-2 3.5 1 .5 3-2 1.5C6.5 14 2 9.5 1.5 3.5z" fill="none" stroke="var(--white)" stroke-width="1.4"/></svg>
          0487 352 019
        </li>
        <li>
          <svg viewBox="0 0 16 16" aria-hidden="true"><rect x="1" y="3" width="14" height="10" fill="none" stroke="var(--white)" stroke-width="1.4"/><path d="M1 3l7 6 7-6" fill="none" stroke="var(--white)" stroke-width="1.4"/></svg>
          tlk@vornamail.net.au
        </li>
      </ul>
    </div>
  </section>

  <section class="card card-back" aria-label="Card back">
    <svg class="card-shape" viewBox="0 0 600 345" aria-hidden="true">
      <path d="M0 0 H22 Q44 6 44 45 V300 Q44 339 22 345 H0 Z" fill="var(--card-black)"/>
      <path d="M600 0 H578 Q556 6 556 45 V300 Q556 339 578 345 H600 Z" fill="var(--card-black)"/>
    </svg>
    <div class="back-brand">
      <div class="brand-name">TLK</div>
      <div class="brand-tagline">Tyler Lane Kirk Electrical</div>
    </div>
    <div class="services">
      <div class="services-licence">licenced &amp; insured Residential</div>
      <div class="services-sectors">commercial – industrial – data REC: 61307</div>
    </div>
  </section>

</main>
</body>
</html>
```